I need a flyer made , the flyer can be one page or two pages or three pages . I will be posting this on Instagram and social media platforms. I am a luxury home builder , I am looking to hire a construction project manager . Below are some examples and ideas what can be on the flyer

We’re looking for a construction project manager who’s passionate about building luxury homes at the highest standards
We’re hiring construction project manager
* Experience 5+ years in residential project management with a strong portfolio of completed homes.
* location : Bergen County NJ
* excellent leadership skills, leads teams with confidence and clarity
* communicates seamlessly with architects , engineers, designers and clients
*knows how to manage budgets and timelines without compromising quality
*solves problems with a positive solution first mindset
* pays attention to every detail because in luxury the small things are the big things

Apply now , link in bio or DM to connect.

My logo is attached, my web site www.velstridebuilders.com
My style is modern but still warm and inviting. I like a clean classy look .

Please don’t add any images of chairs or people to the flyer , I do not want people on my flyer. Do not add standard images of offices and houses , we are luxury builders , we build homes over 2 million dollars. Keep a classy , simple modern look . High end .

You can add a white hard hat with my logo on it for a image , this is a suggestion does not have to be on my flyer ,

```html
<!DOCTYPE html>
<html lang="en">
<head>
<meta charset="UTF-8">
<title>Velstride Builders – Construction Project Manager</title>
<link rel="stylesheet" href="https://fonts.googleapis.com/css2?family=Cinzel:wght@400;500&family=Montserrat:wght@500;600&family=Poppins:wght@400;500;600&family=Pinyon+Script&display=swap">
<style>
  :root {
    --ink: #000000;
    --paper: #ffffff;
    --soft-white: #e8e8e8;
    --gold: #ffcc00;
    --gold-text: #ffc400;
    --dash: #8a8a8a;
    --photo-light: #c9ccd6;
    --photo-mid: #9aa3b5;
    --photo-dark: #1a1a1f;
  }
  * { margin: 0; padding: 0; box-sizing: border-box; }
  html, body { width: 1200px; height: 1200px; overflow: hidden; background: var(--ink); }
  .flyer {
    position: relative;
    width: 1200px;
    height: 1200px;
    background: var(--ink);
    color: var(--paper);
    overflow: hidden;
  }
  .brand {
    position: absolute;
    left: 48px;
    top: 62px;
    font-family: "Cinzel", serif;
    font-weight: 400;
    color: var(--paper);
    font-size: 62px;
    line-height: 1.05;
    letter-spacing: 1px;
  }
  .role-tag {
    position: absolute;
    left: 722px;
    top: 84px;
    width: 478px;
    height: 110px;
    background: var(--gold);
    color: var(--ink);
    font-family: "Cinzel", serif;
    font-weight: 500;
    font-size: 45px;
    line-height: 46px;
    text-align: right;
    padding: 10px 30px 0 0;
  }
  .join-line {
    position: absolute;
    right: 44px;
    top: 208px;
    font-family: "Pinyon Script", cursive;
    font-size: 62px;
    color: var(--paper);
    letter-spacing: 3px;
  }
  .headline {
    position: absolute;
    left: 38px;
    top: 322px;
    font-family: "Montserrat", sans-serif;
    font-weight: 600;
    color: var(--soft-white);
  }
  .headline .lead { display: block; font-size: 58px; line-height: 62px; letter-spacing: 1px; }
  .headline .main { display: block; font-size: 120px; line-height: 112px; letter-spacing: 1px; }
  .divider {
    position: absolute;
    left: 0;
    top: 510px;
    width: 590px;
    height: 2px;
  }
  .requirements {
    position: absolute;
    left: 42px;
    top: 541px;
    width: 560px;
    list-style: none;
    font-family: "Poppins", sans-serif;
    font-size: 17.5px;
    line-height: 28px;
    color: var(--paper);
  }
  .requirements li {
    position: relative;
    padding-left: 35px;
    margin-bottom: 9px;
  }
  .requirements .tick {
    position: absolute;
    left: 0;
    top: 7px;
    width: 16px;
    height: 16px;
  }
  .requirements .accent { color: var(--gold-text); }
  .apply-button {
    position: absolute;
    left: 41px;
    top: 977px;
    width: 230px;
    height: 76px;
    background: var(--gold);
    color: var(--ink);
    font-family: "Cinzel", serif;
    font-weight: 500;
    font-size: 28px;
    display: flex;
    align-items: center;
    justify-content: center;
  }
  .connect-note {
    position: absolute;
    left: 40px;
    top: 1083px;
    font-family: "Poppins", sans-serif;
    font-weight: 600;
    font-size: 17px;
    color: var(--paper);
  }
  .website {
    position: absolute;
    left: 42px;
    top: 1124px;
    font-family: "Cinzel", serif;
    font-size: 21px;
    letter-spacing: 1.5px;
    color: var(--paper);
  }
  .hero-photo {
    position: absolute;
    left: 618px;
    top: 378px;
    width: 582px;
    height: 822px;
    border-radius: 260px 260px 0 0;
    background:
      radial-gradient(ellipse at 50% 22%, var(--photo-light) 0%, var(--photo-mid) 40%, rgba(26,26,31,0) 72%),
      linear-gradient(180deg, var(--photo-dark) 0%, var(--photo-mid) 55%, var(--photo-light) 100%);
    opacity: 0.9;
  }
</style>
</head>
<body>
<main class="flyer">
  <div class="brand">Velstride<br>Builders</div>

  <div class="role-tag">Construction<br>Project Manager</div>
  <div class="join-line">Join Our Team</div>

  <h1 class="headline">
    <span class="lead">WE ARE</span>
    <span class="main">HIRING!</span>
  </h1>

  <svg class="divider" viewBox="0 0 590 2" aria-hidden="true">
    <line x1="0" y1="1" x2="590" y2="1" stroke="var(--dash)" stroke-width="1.5" stroke-dasharray="9 5"/>
  </svg>

  <ul class="requirements">
    <li><svg class="tick" viewBox="0 0 16 16" aria-hidden="true"><circle cx="8" cy="8" r="6.5" fill="none" stroke="var(--paper)" stroke-width="1.4"/><path d="M4.8 8.2 L7.2 10.5 L14 3.5" fill="none" stroke="var(--paper)" stroke-width="1.6"/></svg><span class="accent">Experience 5+ Years</span> In Residential Project Management With A Strong Portfolio Of Completed Homes.</li>
    <li><svg class="tick" viewBox="0 0 16 16" aria-hidden="true"><circle cx="8" cy="8" r="6.5" fill="none" stroke="var(--paper)" stroke-width="1.4"/><path d="M4.8 8.2 L7.2 10.5 L14 3.5" fill="none" stroke="var(--paper)" stroke-width="1.6"/></svg><span class="accent">Location :</span> Bergen County NJ</li>
    <li><svg class="tick" viewBox="0 0 16 16" aria-hidden="true"><circle cx="8" cy="8" r="6.5" fill="none" stroke="var(--paper)" stroke-width="1.4"/><path d="M4.8 8.2 L7.2 10.5 L14 3.5" fill="none" stroke="var(--paper)" stroke-width="1.6"/></svg>Excellent Leadership Skills, Leads Teams With Confidence And Clarity</li>
    <li><svg class="tick" viewBox="0 0 16 16" aria-hidden="true"><circle cx="8" cy="8" r="6.5" fill="none" stroke="var(--paper)" stroke-width="1.4"/><path d="M4.8 8.2 L7.2 10.5 L14 3.5" fill="none" stroke="var(--paper)" stroke-width="1.6"/></svg>Communicates Seamlessly With Architects , Engineers, Designers And Clients</li>
    <li><svg class="tick" viewBox="0 0 16 16" aria-hidden="true"><circle cx="8" cy="8" r="6.5" fill="none" stroke="var(--paper)" stroke-width="1.4"/><path d="M4.8 8.2 L7.2 10.5 L14 3.5" fill="none" stroke="var(--paper)" stroke-width="1.6"/></svg>Knows How To Manage Budgets And Timelines Without Compromising Quality</li>
    <li><svg class="tick" viewBox="0 0 16 16" aria-hidden="true"><circle cx="8" cy="8" r="6.5" fill="none" stroke="var(--paper)" stroke-width="1.4"/><path d="M4.8 8.2 L7.2 10.5 L14 3.5" fill="none" stroke="var(--paper)" stroke-width="1.6"/></svg>Solves Problems With A Positive Solution First Mindset</li>
    <li><svg class="tick" viewBox="0 0 16 16" aria-hidden="true"><circle cx="8" cy="8" r="6.5" fill="none" stroke="var(--paper)" stroke-width="1.4"/><path d="M4.8 8.2 L7.2 10.5 L14 3.5" fill="none" stroke="var(--paper)" stroke-width="1.6"/></svg>Pays Attention To Every Detail Because In Luxury The Small Things Are The Big Things</li>
  </ul>

  <div class="apply-button">Apply now</div>
  <p class="connect-note">Link In Bio Or DM To Connect.</p>
  <p class="website">WWW.VELSTRIDEBUILDERS.COM</p>

  <div class="hero-photo" role="img" aria-label="Photo of a smiling project manager in a white hard hat and glasses holding a tablet"></div>
</main>
</body>
</html>
```